Mens Jewellery Homepage - Modern, Stylish Mens Ring Brand - Homepage

Project Overview: KestrelHoops.com is a men's accessories brand specializing in high-quality mens rings.

The objective of this redesign is to create a modern, visually appealing homepage that is easy to navigate, showcases a wide range of rings, highlights personalization options, and builds trust with customers.

The new design should make a strong impression while reflecting the brand's premium quality and commitment to craftsmanship.

The focus will be on a sleek aesthetic that aligns with the tastes of men shopping for wedding bands, engagement rings, or fashion accessories.

Objectives:

Modern and Sleek Aesthetic:

A clean, minimalist design that emphasizes high-quality product imagery and thoughtful use of space.
Contemporary color palette that conveys elegance and sophistication, with accents that highlight key elements without overwhelming the user.

Consistent and easy-to-read typography that reflects the brand’s modern and masculine identity.

Showcasing Products:
Hero Section: A image to show off 3 or 4 ring designs that could be used for weddings or fashion.

Product Highlights: Below the hero banner, showcase product categories by color (see current website for colors)

Featured Products: Display a selection of “Top Rated” or “Customer Favorites” rings to help guide users toward popular choices.

Personalization Section:
A dedicated section promoting the ability to personalize rings, emphasizing features like engraving with names, dates, or special messages.
Include lifestyle images of personalized rings to inspire customers and give them an idea of what’s possible.
Use callouts such as “Make It Yours” or “Personalize Your Ring” to encourage users to explore the customization options available for each product.

Building Trust:

A space to show 5 or 6 testimonials and other trust elements

Symbols / text to show

free delivery
free returns
every ring stock
fast delivery
customer images (from reviews)

Driving Conversions:
Include a prominent call-to-action (CTA) button in the hero section with text like “Shop Now” or “Discover Our Collections.”

User Experience:
Fast, easy-to-navigate layout with simple and intuitive categories. Product categories and main sections should be clearly visible and easy to access without overwhelming the user.
Design the homepage to feel cohesive and uncluttered, with a logical flow from product discovery to personalization and checkout.

Visual Elements and Imagery:
Use ring images from our site, but add backgrounds etc to make the image on the homepage more interesting.

Personalization Options: Use visual representations (like ring mockups) showing where personalization options (such as engravings) would appear on the product.

I like (and would like to see some different designs from our current design)
Vorm.com for design
ridgeloops.com

Target Market(s)

Men - 20 to 35

Number of Pages Required

1 page

Requirements
Must have
• Easy navigation, Trust, Modern, Clean,
Nice to have
• Would like to see Different designs like Vorm.com - RidgeLoops.com

```html
<!DOCTYPE html>
<html lang="en">
<head>
<meta charset="utf-8">
<title>Kestrel Hoops – Men's Rings</title>
<link href="https://fonts.googleapis.com/css2?family=Playfair+Display:wght@400&family=Josefin+Sans:wght@400;600&display=swap" rel="stylesheet">
<style>
:root{
  --peach:#fcd6aa;
  --peach-soft:#f7d3ab;
  --ink:#111111;
  --card:#f5f5f5;
  --muted:#9a9a9a;
  --footer:#0b0b0b;
  --white:#ffffff;
  --line:#dddddd;
}
*{box-sizing:border-box;margin:0;padding:0}
html,body{width:1200px;height:3563px;overflow:hidden}
body{position:relative;background:var(--white);color:var(--ink);font-family:"Josefin Sans",sans-serif}
.abs{position:absolute}
.serif{font-family:"Playfair Display",serif;font-weight:400}

/* header + hero */
.hero{left:0;top:0;width:1200px;height:597px;background:linear-gradient(100deg,#f6d0a8 0%,#f3c99d 45%,#f7d6b2 100%)}
.hero-photo{left:0;top:0;width:1200px;height:597px;background:radial-gradient(ellipse at 45% 60%,rgba(230,180,140,.55),rgba(246,208,168,0) 60%)}
.logo{display:flex;align-items:center;gap:12px}
.logo-mark{width:70px;height:70px;border:4px solid var(--ink);border-radius:50%}
.logo-text{font-weight:600;letter-spacing:9px;font-size:22px;line-height:1.2}
.logo-text span{display:block;font-size:14px;letter-spacing:13px;padding-left:30px}
.nav{top:64px;left:602px;display:flex;gap:36px;font-size:17px}
.nav-icons{top:59px;left:1051px;display:flex;gap:24px}
.icon-btn{width:32px;height:32px;border-radius:50%;background:var(--ink);display:flex;align-items:center;justify-content:center}
.hero-title{left:68px;top:228px;font-size:64px;line-height:80px}
.btn{display:flex;align-items:center;justify-content:center;background:var(--white);font-size:17px;color:var(--ink)}
.hero-cta{left:62px;top:429px;width:231px;height:41px}
.hero-rings{left:716px;top:240px;width:420px;height:240px;border-radius:8px;background:linear-gradient(180deg,rgba(255,255,255,0) 0%,rgba(20,20,20,.85) 55%,#0d0d0d 100%)}

/* section headings */
.section-title{width:1200px;left:0;text-align:center;font-size:44px}
.arrows{display:flex;gap:10px}
.arrow{width:40px;height:40px;border:1.5px solid var(--ink);border-radius:50%;display:flex;align-items:center;justify-content:center}

/* product cards */
.card{background:var(--card)}
.card-name{position:absolute;font-size:20px}
.heart{position:absolute;width:32px;height:32px;border-radius:50%;background:var(--white);border:1px solid var(--line);display:flex;align-items:center;justify-content:center}
.ring-img{position:absolute;border-radius:50%}
.card-btn{position:absolute;height:40px;font-size:17px}
.ring-black{background:radial-gradient(circle at 40% 40%,#555,#111 60%)}
.ring-silver{background:radial-gradient(circle at 40% 40%,#f2f2f2,#9a9a9a 65%)}
.ring-gold{background:radial-gradient(circle at 40% 40%,#fff2a8,#d6a93a 65%)}
.ring-blue{background:radial-gradient(circle at 40% 40%,#8fa0b5,#1a3fa8 65%)}
.ring-rose{background:radial-gradient(circle at 40% 40%,#f4c9a8,#c98a5e 65%)}
.ring-wood{background:radial-gradient(circle at 40% 40%,#d9d9d9,#7a3b22 65%)}

/* personalise */
.engrave-photo{left:62px;top:1807px;width:533px;height:471px;background:radial-gradient(circle at 55% 70%,#6b6250 0%,#2f2f2f 45%,#1c1c1c 100%)}
.engrave-panel{left:595px;top:1807px;width:542px;height:471px;background:var(--peach)}
.engrave-title{position:absolute;left:0;top:184px;width:100%;text-align:center;font-size:30px;font-weight:600;line-height:41px;letter-spacing:1px}
.engrave-btn{position:absolute;left:163px;top:308px;width:236px;height:39px}

/* testimonials */
.review{top:2458px;width:209px;height:362px;border:1.5px solid #d6d6d6;background:var(--white)}
.review-head{height:97px;border-bottom:1px solid #e3e3e3;display:flex;align-items:center;gap:12px;padding-left:37px;font-size:13px;font-weight:600}
.avatar{width:30px;height:30px;border-radius:50%;background:#3a3a3a;color:#ccc;font-size:7px;display:flex;align-items:center;justify-content:center;font-weight:400}
.review-text{padding:38px 20px 0;text-align:center;font-size:13.5px;line-height:16px;height:160px}
.review-meta{display:flex;justify-content:space-between;padding:0 17px;font-size:13px}
.review-meta .star{color:var(--peach);margin-left:6px}
.review-meta .ago{color:#bbb}
.review-btn{position:absolute;left:17px;bottom:20px;width:171px;height:41px;background:var(--peach);display:flex;justify-content:space-between;align-items:center;padding:0 20px;font-size:18px}

/* trust band */
.trust{left:0;top:2892px;width:1200px;height:329px;background:var(--peach)}
.trust-item{position:absolute;top:93px;width:240px;text-align:center}
.trust-icon{width:96px;height:96px;margin:0 auto;border-radius:50%;background:var(--white);display:flex;align-items:center;justify-content:center}
.trust-label{margin-top:50px;font-size:21px;font-weight:600;letter-spacing:.5px}

/* footer */
.footer{left:0;top:3221px;width:1200px;height:342px;background:var(--footer);color:var(--white)}
.footer .logo-mark{border-color:var(--white);width:78px;height:78px}
.footer .logo-text{font-size:25px;letter-spacing:11px}
.footer .logo-text span{font-size:15px;letter-spacing:16px;padding-left:30px}
.foot-info{left:66px;top:164px;font-size:11.5px;line-height:20px}
.foot-col h3{font-weight:400;font-size:18px;color:var(--peach);margin-bottom:22px}
.foot-col ul{list-style:none;font-size:11.5px;line-height:20px}
.foot-col li::before{content:"•";margin-right:8px}
.foot-rule{left:0;top:273px;width:1200px;height:1px;background:#2a2a2a}
.foot-bottom{top:296px;font-size:11.5px}
.pay{left:460px;top:292px;display:flex;gap:6px}
.pay span{width:30px;height:16px;border-radius:3px;background:#d9d9d9}
</style>
</head>
<body>

<section class="hero abs">
  <div class="hero-photo abs" role="img" aria-label="Soft-focus photo of a couple's hands exchanging a ring"></div>
  <div class="logo abs" style="left:64px;top:41px">
    <div class="logo-mark"></div>
    <div class="logo-text">KESTREL<span>HOOPS</span></div>
  </div>
  <nav class="nav abs"><span>Shop By Material</span><span>Shop By Color</span><span>Try At Home</span></nav>
  <div class="nav-icons abs">
    <div class="icon-btn"><svg width="16" height="16" viewBox="0 0 16 16" fill="none" stroke="#fff" stroke-width="1.4"><path d="M1 2h2l2 8h8l2-6H4"/><circle cx="6" cy="13" r="1"/><circle cx="12" cy="13" r="1"/></svg></div>
    <div class="icon-btn"><svg width="14" height="14" viewBox="0 0 14 14" fill="none" stroke="#fff" stroke-width="1.4"><circle cx="7" cy="4.5" r="3"/><path d="M1.5 13c0-3 2.5-4.5 5.5-4.5s5.5 1.5 5.5 4.5"/></svg></div>
  </div>
  <h1 class="hero-title abs serif">Elevate Your Style<br>With Kestrel Hoops</h1>
  <a class="btn hero-cta abs">Discover Our Collections</a>
  <div class="hero-rings abs" role="img" aria-label="Black, gold and silver rings displayed on black pedestals"></div>
</section>

<h2 class="section-title abs serif" style="top:664px">Product</h2>
<div class="arrows abs" style="left:1045px;top:680px">
  <div class="arrow"><svg width="18" height="10" viewBox="0 0 18 10" fill="none" stroke="#111" stroke-width="1.4"><path d="M17 5H1M5 1L1 5l4 4"/></svg></div>
  <div class="arrow"><svg width="18" height="10" viewBox="0 0 18 10" fill="none" stroke="#111" stroke-width="1.4"><path d="M1 5h16M13 1l4 4-4 4"/></svg></div>
</div>

<div class="card abs" style="left:62px;top:785px;width:356px;height:374px">
  <div class="card-name" style="left:27px;top:32px">Black Rings for Men</div>
  <div class="heart" style="left:302px;top:27px"><svg width="14" height="13" viewBox="0 0 14 13" fill="none" stroke="#111" stroke-width="1.3"><path d="M7 12S1 8 1 4.2A3 3 0 0 1 7 3a3 3 0 0 1 6 1.2C13 8 7 12 7 12z"/></svg></div>
  <div class="ring-img ring-black" role="img" aria-label="Black brushed tungsten ring" style="left:128px;top:110px;width:100px;height:150px"></div>
  <a class="btn card-btn" style="left:36px;top:303px;width:284px">View All Product</a>
</div>
<div class="card abs" style="left:426px;top:785px;width:355px;height:374px">
  <div class="card-name" style="left:32px;top:36px">Silver Rings for Men</div>
  <div class="heart" style="left:300px;top:27px"><svg width="14" height="13" viewBox="0 0 14 13" fill="none" stroke="#111" stroke-width="1.3"><path d="M7 12S1 8 1 4.2A3 3 0 0 1 7 3a3 3 0 0 1 6 1.2C13 8 7 12 7 12z"/></svg></div>
  <div class="ring-img ring-silver" role="img" aria-label="Silver brushed titanium ring" style="left:127px;top:120px;width:102px;height:140px"></div>
  <a class="btn card-btn" style="left:35px;top:303px;width:285px">View All Product</a>
</div>
<div class="card abs" style="left:788px;top:785px;width:354px;height:374px">
  <div class="card-name" style="left:29px;top:36px">Gold Rings for Men</div>
  <div class="heart" style="left:300px;top:27px"><svg width="14" height="13" viewBox="0 0 14 13" fill="none" stroke="#111" stroke-width="1.3"><path d="M7 12S1 8 1 4.2A3 3 0 0 1 7 3a3 3 0 0 1 6 1.2C13 8 7 12 7 12z"/></svg></div>
  <div class="ring-img ring-gold" role="img" aria-label="Polished gold ring" style="left:134px;top:110px;width:94px;height:150px"></div>
  <a class="btn card-btn" style="left:35px;top:303px;width:284px">View All Product</a>
</div>

<h2 class="section-title abs serif" style="top:1233px;left:8px">Featured Product</h2>
<div class="arrows abs" style="left:1045px;top:1249px">
  <div class="arrow"><svg width="18" height="10" viewBox="0 0 18 10" fill="none" stroke="#111" stroke-width="1.4"><path d="M17 5H1M5 1L1 5l4 4"/></svg></div>
  <div class="arrow"><svg width="18" height="10" viewBox="0 0 18 10" fill="none" stroke="#111" stroke-width="1.4"><path d="M1 5h16M13 1l4 4-4 4"/></svg></div>
</div>

<div class="card abs" style="left:62px;top:1355px;width:263px;height:373px">
  <div class="card-name" style="width:100%;text-align:center;top:36px">Blue Rings for Men</div>
  <div class="ring-img ring-blue" role="img" aria-label="Blue and silver tungsten ring" style="left:79px;top:120px;width:105px;height:140px"></div>
  <a class="btn card-btn" style="left:28px;top:311px;width:207px">View All Product</a>
</div>
<div class="card abs" style="left:333px;top:1355px;width:263px;height:373px">
  <div class="card-name" style="width:100%;text-align:center;top:36px">Titanium - Rose gold</div>
  <div class="ring-img ring-rose" role="img" aria-label="Rose gold and titanium ring" style="left:94px;top:120px;width:80px;height:140px"></div>
  <a class="btn card-btn" style="left:28px;top:311px;width:207px">View All Product</a>
</div>
<div class="card abs" style="left:604px;top:1355px;width:263px;height:373px">
  <div class="card-name" style="width:100%;text-align:center;top:36px">Brown Wedding Rings</div>
  <div class="ring-img ring-wood" role="img" aria-label="Silver ring with brown wood inlay" style="left:100px;top:116px;width:80px;height:144px"></div>
  <a class="btn card-btn" style="left:28px;top:311px;width:207px">View All Product</a>
</div>
<div class="card abs" style="left:875px;top:1355px;width:261px;height:373px">
  <div class="card-name" style="width:100%;text-align:center;top:36px">Gold Rings for Men</div>
  <div class="ring-img ring-gold" role="img" aria-label="Polished gold ring" style="left:107px;top:120px;width:85px;height:140px"></div>
  <a class="btn card-btn" style="left:28px;top:311px;width:207px">View All Product</a>
</div>

<div class="engrave-photo abs" role="img" aria-label="Gold ring resting on a dark stone plinth in a moody studio scene"></div>
<div class="engrave-panel abs">
  <h2 class="engrave-title">Personalize Your Ring with<br>Unique Engravings</h2>
  <a class="btn engrave-btn">Make It Yours</a>
</div>

<h2 class="section-title abs serif" style="top:2338px;left:4px">Testimonials</h2>
<div class="arrows abs" style="left:1045px;top:2345px">
  <div class="arrow"><svg width="18" height="10" viewBox="0 0 18 10" fill="none" stroke="#111" stroke-width="1.4"><path d="M17 5H1M5 1L1 5l4 4"/></svg></div>
  <div class="arrow"><svg width="18" height="10" viewBox="0 0 18 10" fill="none" stroke="#111" stroke-width="1.4"><path d="M1 5h16M13 1l4 4-4 4"/></svg></div>
</div>

<article class="review abs" style="left:59px">
  <div class="review-head"><div class="avatar">OH</div>Owen Harte</div>
  <p class="review-text">Fan wedding ring substitute for when husband is at work</p>
  <div class="review-meta"><span>5<span class="star">★</span></span><span class="ago">3 days ago</span></div>
  <a class="review-btn">View<svg width="22" height="10" viewBox="0 0 22 10" fill="none" stroke="#111" stroke-width="1.4"><path d="M1 5h20M17 1l4 4-4 4"/></svg></a>
</article>
<article class="review abs" style="left:278px">
  <div class="review-head"><div class="avatar">LB</div>Lewis Brand</div>
  <p class="review-text">I love the idea of a silicone ring, very clever idea!<br>It is very comfortable to wear...</p>
  <div class="review-meta"><span>5<span class="star">★</span></span><span class="ago">4 days ago</span></div>
  <a class="review-btn">View<svg width="22" height="10" viewBox="0 0 22 10" fill="none" stroke="#111" stroke-width="1.4"><path d="M1 5h20M17 1l4 4-4 4"/></svg></a>
</article>
<article class="review abs" style="left:496px">
  <div class="review-head"><div class="avatar">TF</div>Tomas Fielder</div>
  <p class="review-text">My ring is fantastic and super fast delivery. Marta was superb, making ...</p>
  <div class="review-meta"><span>5<span class="star">★</span></span><span class="ago">2 days ago</span></div>
  <a class="review-btn">View<svg width="22" height="10" viewBox="0 0 22 10" fill="none" stroke="#111" stroke-width="1.4"><path d="M1 5h20M17 1l4 4-4 4"/></svg></a>
</article>
<article class="review abs" style="left:713px">
  <div class="review-head"><div class="avatar">NC</div>Nina Calloway</div>
  <p class="review-text">Gorgeous silver wedding band, my partner fell in love with it so worth the money...</p>
  <div class="review-meta"><span>5<span class="star">★</span></span><span class="ago">2 days ago</span></div>
  <a class="review-btn">View<svg width="22" height="10" viewBox="0 0 22 10" fill="none" stroke="#111" stroke-width="1.4"><path d="M1 5h20M17 1l4 4-4 4"/></svg></a>
</article>
<article class="review abs" style="left:932px">
  <div class="review-head"><div class="avatar">RA</div>Ruth Amberley</div>
  <p class="review-text">Fan wedding ring substitute for when husband is at work ...</p>
  <div class="review-meta"><span>5<span class="star">★</span></span><span class="ago">3 days ago</span></div>
  <a class="review-btn">View<svg width="22" height="10" viewBox="0 0 22 10" fill="none" stroke="#111" stroke-width="1.4"><path d="M1 5h20M17 1l4 4-4 4"/></svg></a>
</article>

<section class="trust abs">
  <div class="trust-item" style="left:74px">
    <div class="trust-icon"><svg width="52" height="40" viewBox="0 0 52 40" fill="none" stroke="#111" stroke-width="1.8"><rect x="2" y="8" width="30" height="22"/><path d="M32 14h10l8 8v8H32z"/><circle cx="12" cy="33" r="4"/><circle cx="40" cy="33" r="4"/></svg></div>
    <div class="trust-label">Free delivery</div>
  </div>
  <div class="trust-item" style="left:350px">
    <div class="trust-icon"><svg width="46" height="46" viewBox="0 0 46 46" fill="none" stroke="#111" stroke-width="1.8"><path d="M8 18a16 16 0 0 1 28-6M38 28a16 16 0 0 1-28 6"/><path d="M36 5v7h-7M10 41v-7h7"/><path d="M15 19l8-4 8 4v9l-8 4-8-4z"/></svg></div>
    <div class="trust-label">Free returns</div>
  </div>
  <div class="trust-item" style="left:636px">
    <div class="trust-icon"><svg width="50" height="44" viewBox="0 0 50 44" fill="none" stroke="#111" stroke-width="1.8"><path d="M16 4l9 4v10l-9 4-9-4V8z"/><path d="M7 22l9 4v10l-9 4-9-4"/><path d="M25 22l9 4v10l-9 4-9-4V26z"/><circle cx="38" cy="30" r="7"/><path d="M35 30l2 2 4-4"/></svg></div>
    <div class="trust-label">Every ring stock</div>
  </div>
  <div class="trust-item" style="left:899px">
    <div class="trust-icon"><svg width="52" height="40" viewBox="0 0 52 40" fill="none" stroke="#111" stroke-width="1.8"><rect x="10" y="6" width="24" height="22"/><path d="M34 12h8l8 8v8H34z"/><path d="M2 12h6M2 18h6M4 24h4"/><circle cx="18" cy="32" r="4"/><circle cx="42" cy="32" r="4"/></svg></div>
    <div class="trust-label">Fast delivery</div>
  </div>
</section>

<footer class="footer abs">
  <div class="logo abs" style="left:66px;top:47px">
    <div class="logo-mark"></div>
    <div class="logo-text">KESTREL<span>HOOPS</span></div>
  </div>
  <p class="foot-info abs">© 2024 Kestrel Hoops - 22 Quarry Lane, Eastvale, EV4 7QT<br>Contact 01632 960418 - hello@kestrelhoops.com<br>Quillmoor Ltd - 07731548 - Incorporated on 14 March 2003</p>
  <div class="foot-col abs" style="left:516px;top:61px">
    <h3>Quick Links</h3>
    <ul><li>FREE ring sizer</li><li>FREE Delivery | Returns and Exchanges</li><li>Try at Home</li><li>Ring Engraving</li><li>Contact Us</li><li>Blog</li></ul>
  </div>
  <div class="foot-col abs" style="left:826px;top:61px">
    <h3>Ring Guide</h3>
    <ul><li>The Best Tungsten and Titanium Rings - Full Guide</li><li>How is Tungsten or Titanium Ring Size Measured?</li><li>Black, Silver Gold - The best colors for mens tungsten</li><li>and titanium rings</li><li>Whats better tungsten or titanium for a mens ring</li></ul>
  </div>
  <div class="foot-rule abs"></div>
  <div class="foot-bottom abs" style="left:66px">© Copyright 2024 &nbsp;All Rights Reserved.</div>
  <div class="pay abs" aria-label="Accepted payment methods"><span></span><span></span><span></span><span></span><span></span><span></span><span></span><span></span></div>
  <div class="foot-bottom abs" style="left:935px">Privacy policy</div>
  <div class="foot-bottom abs" style="left:1045px">Terms of Service</div>
</footer>

</body>
</html>
```